Fern Lattice Table & Chair Rentals

We need a business card for a table and chair rental company. We rent tables and chairs for weddings, funerals, business events and parties. We want something that looks clean and elegant while not being too busy. We would like colors in the green and blue hues and avoiding anything orange. We want to make sure the font is large enough to be seen easily.

Target Market(s)

Wedding & Event Rentals

Industry/Entity Type

Events

Contact Information for Business Card

Fern Lattice, sales@fernlatticerentals.com, fernlatticerentals.com, 360-555-0182

Requirements
Must have
• Easy to read font
Should not have
• Orange anywhere in the design

```html
<!DOCTYPE html>
<html lang="en">
<head>
<meta charset="utf-8">
<title>Fern Lattice Table &amp; Chair Rentals – Business Card</title>
<link rel="stylesheet" href="https://fonts.googleapis.com/css2?family=Arimo:wght@400;700&display=swap">
<style>
  :root {
    --page-bg: #e7ebea;
    --paper: #f4f5f5;
    --paper-shade: #e3e6e6;
    --band-light: #3fa3b4;
    --band-mid: #2a8a85;
    --band-deep: #1d5f5c;
    --ink: #23302f;
    --ink-soft: #34403f;
    --on-band: #f2faf8;
    --rule: #3a4544;
  }
  * { box-sizing: border-box; margin: 0; padding: 0; }
  html, body {
    width: 1200px;
    height: 892px;
    overflow: hidden;
    background: var(--page-bg);
    font-family: "Arimo", Arial, sans-serif;
  }
  .sheet {
    width: 1200px;
    height: 892px;
    display: flex;
    align-items: center;
    justify-content: center;
    gap: 40px;
  }
  .card {
    position: relative;
    width: 520px;
    height: 297px;
    overflow: hidden;
    box-shadow: 0 6px 18px rgba(0,0,0,0.18);
    background: var(--paper);
  }
  .band-colour {
    position: absolute;
    left: 0; right: 0;
    background: linear-gradient(115deg, var(--band-deep) 0%, var(--band-mid) 45%, var(--band-light) 100%);
  }
  .band-paper {
    position: absolute;
    left: 0; right: 0;
    background: linear-gradient(100deg, var(--paper) 0%, #ffffff 55%, var(--paper-shade) 100%);
  }

  /* Front */
  .card--front .band-colour { top: 0; height: 160px; }
  .card--front .band-paper { top: 160px; bottom: 0; }
  .front-brand {
    position: absolute;
    left: 30px;
    top: 34px;
  }
  .brand-name {
    font-weight: 700;
    color: var(--ink);
    font-size: 46px;
    line-height: 1;
    letter-spacing: -0.5px;
  }
  .card--front .brand-name { color: var(--on-band); }
  .front-tagline {
    margin-top: 12px;
    font-size: 24px;
    color: var(--on-band);
    font-weight: 400;
  }
  .front-details {
    position: absolute;
    left: 30px;
    right: 0;
    top: 178px;
  }
  .company-legal {
    font-size: 19px;
    color: var(--ink);
    padding-right: 30px;
  }
  .rule {
    margin-top: 8px;
    height: 1px;
    background: var(--rule);
    margin-left: 180px;
  }
  .contact-list {
    list-style: none;
    margin-top: 8px;
    padding-left: 240px;
    font-size: 14px;
    line-height: 1.35;
    color: var(--ink-soft);
  }

  /* Back */
  .card--back .band-paper { top: 0; height: 150px; }
  .card--back .band-colour {
    top: 150px; bottom: 0;
    background: linear-gradient(100deg, var(--band-deep) 0%, var(--band-mid) 45%, var(--band-light) 100%);
  }
  .back-brand {
    position: absolute;
    right: 36px;
    top: 22px;
    text-align: right;
  }
  .back-brand .brand-name { font-size: 36px; }
  .back-tagline {
    margin-top: 6px;
    font-size: 20px;
    color: var(--ink);
  }
  .hours {
    position: absolute;
    left: 24px;
    right: 24px;
    top: 120px;
    font-size: 12px;
    color: var(--ink);
    white-space: nowrap;
  }
</style>
</head>
<body>
<main class="sheet">
  <section class="card card--front" aria-label="Business card front">
    <div class="band-colour"></div>
    <div class="band-paper"></div>
    <div class="front-brand">
      <div class="brand-name">Fern Lattice</div>
      <div class="front-tagline">Table and Chair Rentals</div>
    </div>
    <div class="front-details">
      <div class="company-legal">Fernlattice Event Rentals, LLC</div>
      <div class="rule"></div>
      <ul class="contact-list">
        <li>360-555-0182</li>
        <li>www.fernlatticerentals.com</li>
        <li>sales@fernlatticerentals.com</li>
      </ul>
    </div>
  </section>

  <section class="card card--back" aria-label="Business card back">
    <div class="band-paper"></div>
    <div class="band-colour"></div>
    <div class="back-brand">
      <div class="brand-name">Fern Lattice</div>
      <div class="back-tagline">Table and Chair Rentals</div>
    </div>
    <p class="hours">Mon-Fri: 8am to 6pm - Saturday: 8am to 4pm - Sunday: 9am to 1pm</p>
  </section>
</main>
</body>
</html>
```